Varsity Purse Wordpress Website (re)design

we are a student run financial literacy website and are desperately trying to get college students to pay attention to the finances to create solid financial skills for life. This age group LOVES pixolette so instead of sharing a lot of text we want to tease through graphics/infographics topics that are relevant to them based on what their peers are discussing and then push them to our resources to learn more. ultimately we will also recommend products to them that are carefully selected by us. these will range from a book on paying back their student loan to a place to store their dorm stuff when they go home for summer break to a credit card we determine is best for them. So yes, commerce is imp but SEO to attract students comes first which we will do through survey monkey and cash prizes. we need to capture email address. we also have a "checklist" (attached and needs rebranding) of the basic and most imp money matters for them. Each item will hyperlink to our parnter, nuvoe, and need to do so seamlessly and push them back to us.

Target Market(s)

college students and young adults

Requirements
Must have
• simple, clean and graphic with an integration of survey monkey, an borvel store and a capture of emails through mailchimp or other similar. Ability to edit after ourselves on wordpress

```html
<!DOCTYPE html>
<html lang="en">
<head>
<meta charset="utf-8">
<title>Varsity Purse – Take Charge of Your Change</title>
<link rel="stylesheet" href="https://fonts.googleapis.com/css2?family=Montserrat:wght@500;600;700;800&family=Open+Sans:ital,wght@0,400;0,600;0,700;1,400&display=swap">
<style>
:root{
  --blue:#2a7bb1;
  --blue-text:#2b7fbd;
  --green:#5cb531;
  --ink:#1f1f1f;
  --muted:#6e6e6e;
  --line:#cfcfcf;
  --mint:#eefafc;
  --teal:#1e8b8f;
  --footer:#1c1c1c;
  --social-1:#4a2fd0;
  --social-2:#27b6d9;
  --social-3:#d8685c;
  --social-4:#3a4fa8;
}
*{box-sizing:border-box;margin:0;padding:0}
html,body{width:1200px;height:3533px;overflow:hidden;background:#fff}
body{position:relative;font-family:"Open Sans",sans-serif;color:var(--ink)}
.abs{position:absolute}
a{color:inherit;text-decoration:none}

/* header */
.site-header{position:absolute;left:0;top:0;width:1200px;height:96px;background:#fff}
.brand{position:absolute;left:117px;top:26px;display:flex;align-items:center;gap:10px;font-family:"Open Sans",sans-serif;font-weight:600;font-size:32px;color:var(--blue)}
.brand-dot{width:26px;height:26px;border-radius:50%;background:var(--green)}
.main-nav{position:absolute;left:505px;top:38px;display:flex;gap:24px;font-family:"Open Sans",sans-serif;font-weight:600;font-size:15px;color:#222}
.main-nav .active{color:var(--blue-text)}
.btn{display:inline-block;background:var(--green);color:#fff;font-family:"Montserrat",sans-serif;font-weight:700;text-transform:uppercase}
.login{position:absolute;left:994px;top:33px;width:96px;height:30px;line-height:30px;text-align:center;font-size:15px}

/* hero */
.hero{position:absolute;left:0;top:96px;width:1200px;height:710px;
  background:linear-gradient(100deg,#2c2a24 0%,#5b5140 30%,#8a7a5e 55%,#6b5a44 75%,#3c3528 100%);
  clip-path:polygon(0 0,100% 0,100% 609px,855px 710px,0 609px)}
.hero-title{position:absolute;left:115px;top:330px;font-family:"Montserrat",sans-serif;font-weight:800;font-size:69px;line-height:85px;color:#fff;text-transform:uppercase}
.dots{position:absolute;left:815px;top:721px;display:flex;gap:6px}
.dots span{width:11px;height:11px;border-radius:50%;background:#fff}
.dots span.on{background:#4aa3df}

/* welcome */
.welcome-title{position:absolute;left:0;top:882px;width:1200px;text-align:center;font-family:"Montserrat",sans-serif;font-weight:600;font-size:38px;color:#111}
.welcome-text{position:absolute;left:0;top:955px;width:1200px;text-align:center;font-size:21px;line-height:29px;color:#222}
.cards{position:absolute;left:110px;top:1103px;width:980px;height:320px;border:1px solid var(--line)}
.card-art{position:absolute;border-radius:4px}
.card-label{position:absolute;text-align:center;font-size:21px;line-height:28px;color:#222}
.card-feature{position:absolute;left:412px;top:1066px;width:376px;height:394px;background:#fff;box-shadow:0 2px 10px rgba(0,0,0,.18);text-align:center}
.card-feature .card-art{left:143px;top:40px;width:90px;height:90px;background:linear-gradient(135deg,#dcecf6,#d6efcb)}
.card-feature h3{position:absolute;left:0;top:164px;width:100%;font-family:"Open Sans",sans-serif;font-weight:400;font-size:22px;line-height:28px}
.card-feature p{position:absolute;left:24px;top:238px;width:328px;font-size:13.5px;line-height:28px;color:var(--muted)}
.card-feature .more{position:absolute;left:0;top:341px;width:100%;font-weight:700;font-size:16px;color:var(--blue-text)}

/* course band */
.course-photo{position:absolute;left:0;top:1559px;width:601px;height:436px;background:linear-gradient(135deg,#4a3b27 0%,#7b6850 40%,#cbbf9f 70%,#3a3227 100%)}
.course-panel{position:absolute;left:601px;top:1559px;width:599px;height:436px;background:var(--blue);color:#fff}
.course-panel h2{position:absolute;left:89px;top:40px;font-family:"Montserrat",sans-serif;font-weight:600;font-size:38px;line-height:40px}
.course-panel p{position:absolute;left:89px;width:420px;font-size:13.5px;line-height:28px}
.course-panel .lead{top:142px}
.course-panel .strong{top:243px;font-weight:600;font-size:15px;width:430px}
.course-panel .btn{position:absolute;left:89px;top:330px;width:126px;height:38px;line-height:38px;text-align:center;font-size:16px}

/* tips */
.tips{position:absolute;left:0;top:1995px;width:1200px;height:635px;background:var(--mint)}
.tips h2{position:absolute;left:113px;top:140px;font-family:"Montserrat",sans-serif;font-weight:600;font-size:38px}
.tips .intro{position:absolute;left:110px;top:206px;width:500px;font-size:21px;line-height:28px}
.tips ul{position:absolute;left:112px;top:300px;list-style:none;font-size:13.5px;color:var(--muted)}
.tips li{height:39px;display:flex;align-items:flex-start;gap:6px}
.tips li::before{content:"";width:9px;height:9px;margin-top:5px;border:2px solid var(--teal);border-radius:50%;flex:none}
.tips .btn{position:absolute;left:111px;top:465px;width:126px;height:38px;line-height:38px;text-align:center;font-size:16px}
.checklist{position:absolute;left:668px;top:2028px;width:411px;height:567px;background:#fff;box-shadow:0 1px 6px rgba(0,0,0,.25);padding:8px}
.checklist div{width:100%;height:100%;background:linear-gradient(180deg,#e6ecf8 0%,#a9c4ee 18%,#9fbdf0 90%,#f4f4f4 100%)}

/* testimonials */
.testimonials{position:absolute;left:110px;top:2703px;width:980px;height:332px;border:1px solid #a9a9a9;text-align:center}
.testimonials h2{position:absolute;left:0;top:42px;width:100%;font-family:"Montserrat",sans-serif;font-weight:700;font-size:38px}
.testimonials blockquote{position:absolute;left:80px;top:112px;width:820px;font-style:italic;font-size:18.5px;line-height:28px;color:#555}
.avatar{position:absolute;left:348px;top:222px;width:76px;height:76px;border-radius:50%;background:linear-gradient(160deg,#d7dde4,#3b4a63)}
.author{position:absolute;left:440px;top:236px;text-align:left;font-family:"Montserrat",sans-serif;font-weight:600;font-size:20px}
.role{position:absolute;left:445px;top:268px;font-weight:600;font-size:17px}
.arrow{position:absolute;top:2843px;width:32px;height:65px;background:#8c8c8c;display:flex;align-items:center;justify-content:center}

/* footer */
.site-footer{position:absolute;left:0;top:3115px;width:1200px;height:418px;background:linear-gradient(180deg,#232323,#151515);
  clip-path:polygon(0 95px,345px 0,100% 95px,100% 100%,0 100%)}
.footer-brand{position:absolute;left:117px;top:3260px;display:flex;align-items:center;gap:10px;font-weight:600;font-size:34px;color:#fff}
.social{position:absolute;left:117px;top:3333px;display:flex;gap:11px}
.social span{width:40px;height:40px;border-radius:50%}
.footer-nav{position:absolute;left:423px;top:3262px;list-style:none;font-weight:600;font-size:15px;color:#fff;line-height:28px}
.footer-cta{position:absolute;left:642px;top:3262px;color:#fff;width:448px}
.footer-cta h3{font-family:"Montserrat",sans-serif;font-weight:500;font-size:22px}
.footer-cta p{margin-top:10px;width:370px;font-size:13.5px;line-height:28px}
.email{position:absolute;left:642px;top:3363px;width:448px;height:37px;background:#fff;display:flex;align-items:center;gap:8px;padding-left:22px;font-size:14px;color:#333}
.submit{position:absolute;left:643px;top:3420px;width:102px;height:30px;line-height:30px;text-align:center;font-size:15px;font-family:"Open Sans",sans-serif}
.copyright{position:absolute;left:0;top:3491px;width:1200px;text-align:center;font-size:13.5px;color:#fff}
</style>
</head>
<body>

<header class="site-header">
  <a class="brand" href="#"><span class="brand-dot"></span>Varsity Purse</a>
  <nav class="main-nav">
    <a class="active" href="#">HOME</a><a href="#">OUR WORK</a><a href="#">BLOG</a><a href="#">TIPS&amp;TRICKS</a><a href="#">ABOUT NUVOE</a>
  </nav>
  <a class="btn login" href="#">Login</a>
</header>

<section class="hero" role="img" aria-label="Photo of college students laughing around a laptop on outdoor steps"></section>
<h1 class="hero-title">Take charge of<br>your change</h1>
<div class="dots"><span></span><span class="on"></span><span></span></div>

<h2 class="welcome-title">WELCOME TO VARSITY PURSE!</h2>
<p class="welcome-text">Welcome to your FREE resource that will help you achieve<br>financial independence and knowledge.</p>

<div class="cards"></div>
<div class="card-art" style="left:200px;top:1183px;width:128px;height:112px;background:linear-gradient(135deg,#dcecf6,#d6efcb)" role="img" aria-label="Illustration for the budgeting topic"></div>
<p class="card-label" style="left:110px;top:1312px;width:306px">How To Budget</p>
<div class="card-art" style="left:867px;top:1185px;width:139px;height:116px;background:linear-gradient(135deg,#e8f4f5,#bfe3c7)" role="img" aria-label="Illustration for the side hustle topic"></div>
<p class="card-label" style="left:784px;top:1312px;width:306px">How To Create<br>Own Side Hustle</p>

<article class="card-feature">
  <div class="card-art" role="img" aria-label="Illustration for the money saving topic"></div>
  <h3>Money Saving Hacks<br>For Millennials</h3>
  <p>The other generations love to pick on us, but the unemployment rate is the lowest it’s been in over 50 years, so it’s good to be a millennial!</p>
  <a class="more" href="#">READ MORE&gt;&gt;</a>
</article>

<div class="course-photo" role="img" aria-label="Photo of a hand with a pencil using a calculator over a notebook"></div>
<section class="course-panel">
  <h2>Why Take A Personal<br>Finance Course?</h2>
  <p class="lead">Varsity Purse will teach you how to use your student loan get a new car, how to fill out those first day of work tax forms without calling mom and dad,</p>
  <p class="strong">Personal financial skills will keep your wallet full and your options open Take charge of your finances today</p>
  <a class="btn" href="#">Read more</a>
</section>

<section class="tips">
  <h2>Tips &amp; Tricks</h2>
  <p class="intro">Sed ut perspiciatis unde omnis iste natus error fugit,&nbsp; quia consequuntur mvoluptatem</p>
  <ul>
    <li>Lorem ipsum dolor sit amet, consectetur adipiscing elit</li>
    <li>sed do eiusmod tempor incididunt ut labore et dolore magna aliqua.</li>
    <li>Ang Lorem Ipsum ay gin industriya ng pagpriprint at pagtytypeset.</li>
    <li>Lorem ipsum dolor sit amet, consectetur adipiscing elit</li>
  </ul>
  <a class="btn" href="#">Read more</a>
</section>
<figure class="checklist"><div role="img" aria-label="Infographic: college and beyond money checklist with nine topic columns"></div></figure>

<section class="testimonials">
  <h2>TESTIMONIALS</h2>
  <blockquote>“In today’s extra competitive job market, college students need a leg up. Financial literacy skills, like those taught at Varsity Purse, are the answer. Financial literacy provides an important advantage in finding a job and is a skill that will help students throughout their lives.”</blockquote>
  <div class="avatar" role="img" aria-label="Portrait of the quoted speaker"></div>
  <p class="author">– Daniel Whitmore</p>
  <p class="role">Founder of Northwind Group</p>
</section>
<a class="arrow" style="left:78px" href="#" aria-label="Previous"><svg width="14" height="20" viewBox="0 0 14 20"><path d="M11 2 3 10l8 8" stroke="#fff" stroke-width="3" fill="none"/></svg></a>
<a class="arrow" style="left:1090px" href="#" aria-label="Next"><svg width="14" height="20" viewBox="0 0 14 20"><path d="m3 2 8 8-8 8" stroke="#fff" stroke-width="3" fill="none"/></svg></a>

<footer class="site-footer" role="img" aria-label="Dim photo of students in the background"></footer>
<a class="footer-brand" href="#"><span class="brand-dot"></span>Varsity Purse</a>
<div class="social">
  <span style="background:var(--social-1)" aria-label="Social profile one"></span>
  <span style="background:var(--social-2)" aria-label="Social profile two"></span>
  <span style="background:var(--social-3)" aria-label="Pixolette profile"></span>
  <span style="background:var(--social-4)" aria-label="Social profile four"></span>
</div>
<ul class="footer-nav"><li>HOME</li><li>WORK</li><li>BLOG</li><li>TIPS&amp;TRICKS</li><li>ABOUT NUVOE</li></ul>
<div class="footer-cta">
  <h3>TAKE CHARGE OF YOUR CHANGE</h3>
  <p>You may reach us at any time for general inquiries or other questions. We look forward to hearing from you!</p>
</div>
<label class="email"><svg width="14" height="11" viewBox="0 0 14 11" fill="none" stroke="#333" stroke-width="1.4"><rect x="1" y="1" width="12" height="9"/><path d="m1 1 6 5 6-5"/></svg>Enter email</label>
<a class="btn submit" href="#">SUBMIT</a>
<p class="copyright">Copyright © 2019 All rights reserved | varsity purse</p>

</body>
</html>
```